Brightleaf Rx Pass reinvent our website.

Our Website is outdated and needs an overhaul, in every aspect. We assist individuals that have little or no prescription coverage and allow them to receive a discount ranging from 33% up to 78% for free. In the beginning we utilized pharmacies to spread the word, but times have a changed. We are looking for a modern and clean site. We are open to anything, image, logo etc.

Target Market(s)

Anyone regardless of residency, age or income. This program is designed to assist those that have NO prescription coverage or for those whose particular prescription may not be covered by insurance.

Industry/Entity Type

Pharmaceutical

Coding

Coded - Design and coding required

Number of Pages Required

4 page

Requirements
Must have
• -The two MUST haves are the pharmacy locators & drug pricing. If you can combine the 2, even better.
• -a ongoing counter/tally on the 1stpage reflecting the amount of money we are saving customers. http://widgetmarto.net/item/motion-tickers-v-20-flux-pack-collection/full_screen_preview/52907314
• -on a smart phone the ability to view the information that is needed to get the actual discount for the medication.
Nice to have
• animated tutorial showing how to use the card
• health blog

```html
<!DOCTYPE html>
<html lang="en">
<head>
<meta charset="utf-8">
<title>Brightleaf Rx Pass</title>
<link rel="stylesheet" href="https://fonts.googleapis.com/css2?family=Open+Sans:wght@400;600;700&display=swap">
<style>
:root{
  --blue:#1a4f98;
  --blue-dark:#143f7c;
  --red:#e4332c;
  --ink:#2b2b2b;
  --muted:#6d6d6d;
  --line:#dcdcdc;
  --band:#eceff5;
  --white:#ffffff;
}
*{box-sizing:border-box;margin:0;padding:0}
html,body{width:1200px;height:2326px;overflow:hidden;background:var(--white)}
body{position:relative;font-family:"Open Sans",Arial,sans-serif;color:var(--ink)}
.abs{position:absolute}
.top-rule{left:0;top:0;width:1200px;height:5px;background:var(--blue)}
.brand{left:100px;top:34px;display:flex;align-items:center;gap:10px;font-size:24px;font-weight:700;color:var(--blue)}
.brand-dot{width:26px;height:26px;border-radius:50%;background:var(--red)}
.nav{left:383px;top:5px;height:91px;display:flex;align-items:center;font-size:14px;font-weight:600;text-transform:uppercase}
.nav a{color:var(--ink);text-decoration:none;padding:0 28px;height:91px;display:flex;align-items:center}
.nav a.active{background:var(--blue);color:var(--white);padding:0 12px;width:68px;justify-content:center}
.search{left:1068px;top:38px;width:30px;height:30px;border-radius:50%;background:var(--blue)}
.hero{left:0;top:96px;width:1200px;height:606px;background:linear-gradient(100deg,#c9ccd0 0%,#e2e0dc 40%,#f2efec 60%,#d8d5d2 100%)}
.hero-arrow{top:378px;width:46px;height:46px;border-radius:50%;background:rgba(90,110,140,.55)}
.hero-card{left:100px;top:338px;width:532px;height:256px;background:rgba(255,255,255,.82);border-left:5px solid var(--blue);padding:24px 0 0 18px}
.hero-card h1{font-size:21px;font-weight:600;color:var(--red);letter-spacing:.3px;margin-bottom:10px}
.hero-card p{font-size:14px;line-height:24px;color:#333}
.hero-card strong{color:var(--red)}
.btn-free{display:flex;margin-top:16px;height:38px;width:148px;font-size:13px;font-weight:700}
.btn-free span:first-child{background:var(--blue);color:var(--white);border-radius:19px 0 0 19px;width:84px;display:flex;align-items:center;justify-content:center;border-radius:19px}
.btn-free span:last-child{border:1.5px solid var(--red);color:var(--red);border-radius:0 19px 19px 0;flex:1;display:flex;align-items:center;padding-left:12px;margin-left:-12px}
.section-title{font-size:19px;font-weight:400;color:var(--ink);letter-spacing:.3px}
.title-rule{height:2px;background:var(--blue);width:76px}
.body-text{font-size:12.5px;line-height:25px;color:var(--muted)}
.read-more{left:99px;top:952px;font-size:14px;font-weight:700;color:var(--blue)}
.video{left:762px;top:806px;width:338px;height:206px;background:linear-gradient(120deg,#3a3a3a,#6b6a68 60%,#8a7f78);}
.video-bar{left:762px;top:972px;width:338px;height:40px;background:#111}
.rule{height:1px;background:var(--line)}
.blog-arrow{top:1095px;width:24px;height:24px;border-radius:50%;border:1.5px solid var(--blue)}
.post{width:300px}
.post-img{height:182px}
.post h3{font-size:16px;font-weight:400;margin:24px 0 8px;color:var(--ink)}
.post p{font-size:12.5px;line-height:22px;color:var(--muted)}
.question{left:0;top:1469px;width:1200px;height:146px;background:var(--band)}
.quote-btn{left:835px;top:1513px;width:262px;height:62px;background:var(--blue-dark);border:3px solid #3a6ab0;color:var(--white);font-size:24px;display:flex;align-items:center;justify-content:center;font-family:Arial,sans-serif}
.prices-title{left:99px;top:1668px;font-size:22px;color:var(--red)}
.price-label{font-size:13px;color:var(--muted)}
.price-val{font-size:18px;color:var(--red)}
.pills{left:682px;top:1705px;width:418px;height:248px;border-radius:40%;background:radial-gradient(ellipse at center,#e7609a 0%,#3c6cd6 55%,rgba(255,255,255,0) 72%)}
.contact-ico{top:2070px;width:46px;height:46px;background:var(--blue);border-radius:4px}
.vsep{top:2040px;width:1px;height:102px;background:var(--line)}
.c-label{font-size:12.5px;font-weight:600;color:#444;letter-spacing:.5px}
.c-value{font-size:18px;font-weight:700;color:var(--blue)}
.c-small{font-size:11.5px;color:#999;letter-spacing:.8px;line-height:25px}
.footer{left:0;top:2173px;width:1200px;height:153px;background:var(--blue)}
.foot-nav{left:0;top:2193px;width:1200px;display:flex;justify-content:center;gap:28px;font-size:12.5px;font-weight:600;color:var(--white)}
.social{top:2231px;width:36px;height:36px;border-radius:50%;background:#5a8fd4;border:3px solid var(--white)}
.copy{left:0;top:2286px;width:1200px;text-align:center;font-size:12px;color:#dbe5f4}
</style>
</head>
<body>
<div class="abs top-rule"></div>
<div class="abs brand"><span class="brand-dot"></span>Brightleaf Rx Pass</div>
<nav class="abs nav">
  <a class="active">Home</a><a>Get card</a><a>FAQ</a><a>Pharmacies</a><a>Drug pricing</a><a>Contact</a>
</nav>
<div class="abs search"><svg width="30" height="30" viewBox="0 0 30 30"><circle cx="14" cy="14" r="5" fill="none" stroke="#fff" stroke-width="2"/><line x1="18" y1="18" x2="21" y2="21" stroke="#fff" stroke-width="2"/></svg></div>

<div class="abs hero" role="img" aria-label="Smiling pharmacist in a white coat in front of pharmacy shelves"></div>
<div class="abs hero-arrow" style="left:32px"><svg width="46" height="46"><polyline points="27,14 19,23 27,32" fill="none" stroke="#fff" stroke-width="2"/></svg></div>
<div class="abs hero-arrow" style="left:1124px"><svg width="46" height="46"><polyline points="19,14 27,23 19,32" fill="none" stroke="#fff" stroke-width="2"/></svg></div>
<div class="abs hero-card">
  <h1>FREE PRESCRIPTION ASSISTANCE PROGRAM</h1>
  <p>Completely Free prescription Assistance Program Lowest Price logic to<br>guarantee that you get the best deal on your prescriptions<br>Instant Printable membership card ready to use<br>Saving of up to <strong>75%</strong> at more than <strong>60,000</strong> national and regional pharmacies<br>This card is pre-activate and can be used immediately</p>
  <div class="btn-free"><span>GET FREE</span><span>CARD</span></div>
</div>

<h2 class="abs section-title" style="left:99px;top:752px">OUR MISSION</h2>
<div class="abs title-rule" style="left:99px;top:789px"></div>
<div class="abs rule" style="left:175px;top:790px;width:45px"></div>
<p class="abs body-text" style="left:99px;top:810px;width:620px">Lorem ipsum dolor sit amet, consectetur adipiscing elit, sed do eiusmod tempor incididunt ut labore et dolore magna aliqua. Ut enim ad minim veniam,<br>uis nostrud exercitation ullamco laboris nisi ut aliquip ex ea commodo consequat. Duis aute irure dolor in reprehenderit in voluptate velit esse cillum dolore eu fugiat. nulla pariatur Sed ut perspiciatis unde omnis iste natus error sit voluptatem accusantium doloremque laudantium.</p>
<div class="abs read-more">Read more....</div>

<h2 class="abs section-title" style="left:761px;top:750px">How to use the card</h2>
<div class="abs title-rule" style="left:761px;top:789px;width:112px"></div>
<div class="abs rule" style="left:873px;top:790px;width:120px"></div>
<div class="abs video" role="img" aria-label="Tutorial video still showing a hand holding the discount card"></div>
<svg class="abs" style="left:908px;top:886px" width="46" height="46"><circle cx="23" cy="23" r="22" fill="#fff"/><polygon points="18,13 32,23 18,33" fill="#333"/></svg>
<div class="abs video-bar"></div>
<div class="abs" style="left:770px;top:974px;width:322px;height:3px;background:#555"><div style="width:180px;height:3px;background:var(--red)"></div></div>
<svg class="abs" style="left:780px;top:990px" width="310" height="16">
  <polygon points="2,2 12,8 2,14" fill="#fff"/><polygon points="32,3 38,8 32,13" fill="#fff"/><polygon points="38,3 44,8 38,13" fill="#fff"/><rect x="44" y="3" width="2" height="10" fill="#fff"/>
  <polygon points="62,6 66,6 70,2 70,14 66,10 62,10" fill="#fff"/>
  <text x="88" y="12" font-size="9" fill="#fff" font-family="Arial,sans-serif">2:42 / 4:29</text>
  <circle cx="240" cy="8" r="5" fill="none" stroke="#fff" stroke-width="2"/><rect x="262" y="3" width="14" height="10" fill="none" stroke="#fff" stroke-width="2"/><rect x="288" y="2" width="14" height="12" fill="none" stroke="#fff" stroke-width="2" stroke-dasharray="4 6"/>
</svg>

<div class="abs rule" style="left:99px;top:1056px;width:1002px"></div>

<h2 class="abs section-title" style="left:104px;top:1094px">Health blog</h2>
<div class="abs rule" style="left:99px;top:1136px;width:1002px"></div>
<div class="abs title-rule" style="left:104px;top:1135px"></div>
<div class="abs blog-arrow" style="left:1040px"><svg width="21" height="21"><polyline points="12,6 8,10.5 12,15" fill="none" stroke="#1a4f98" stroke-width="1.8"/></svg></div>
<div class="abs blog-arrow" style="left:1072px"><svg width="21" height="21"><polyline points="9,6 13,10.5 9,15" fill="none" stroke="#1a4f98" stroke-width="1.8"/></svg></div>

<article class="abs post" style="left:105px;top:1153px">
  <div class="post-img" role="img" aria-label="Yellow and red capsules scattered on a white surface" style="background:linear-gradient(135deg,#e8e8d8,#b8b83a 50%,#f0f0f0)"></div>
  <h3>Lorem ipsum dolor sit amet</h3>
  <p>Lorem ipsum dolor sit amet, consectetur adipisc-<br>ing elit, sed do eiusmod tempor incididunt</p>
</article>
<article class="abs post" style="left:451px;top:1153px">
  <div class="post-img" role="img" aria-label="White pill and orange bottle on a heart rate chart" style="background:linear-gradient(135deg,#f3eeea,#f5c9a8 60%,#e87a2c)"></div>
  <h3>Lorem ipsum dolor sit amet</h3>
  <p>Lorem ipsum dolor sit amet, consectetur adipisc-<br>ing elit, sed do eiusmod tempor incididunt</p>
</article>
<article class="abs post" style="left:795px;top:1153px">
  <div class="post-img" role="img" aria-label="Colourful pills spilling from an amber bottle" style="background:linear-gradient(135deg,#f4b320,#f6d9a8 45%,#9ad0e8 75%,#f0f0f0)"></div>
  <h3>Lorem ipsum dolor sit amet</h3>
  <p>Lorem ipsum dolor sit amet, consectetur adipisc-<br>ing elit, sed do eiusmod tempor incididunt</p>
</article>

<section class="abs question"></section>
<h2 class="abs section-title" style="left:98px;top:1494px;font-size:22px">Have a question ?</h2>
<p class="abs body-text" style="left:99px;top:1533px;width:640px">Lorem ipsum dolor sit amet, consectetur adipiscing elit, sed do eiusmod tempor incididunt ut labore et dolore magna aliqua. Ut enim ad minim veniam,</p>
<div class="abs quote-btn">Get a quot now</div>

<h2 class="abs prices-title">PRICES</h2>
<p class="abs" style="left:100px;top:1703px;font-size:14px;color:#444">The Drug - Wich is Marketed under several brand.</p>
<svg class="abs" style="left:492px;top:1675px" width="48" height="48"><circle cx="24" cy="24" r="21" fill="none" stroke="#e4332c" stroke-width="3"/><text x="24" y="32" text-anchor="middle" font-size="24" font-weight="700" fill="#e4332c" font-family="Arial,sans-serif">$</text></svg>
<div class="abs rule" style="left:99px;top:1734px;width:440px"></div>

<div class="abs price-label" style="left:99px;top:1752px">20 Tablets (2Weeks Supply)</div>
<div class="abs price-val" style="left:102px;top:1777px">$40</div>
<div class="abs price-label" style="left:353px;top:1752px;width:183px;text-align:right">80 Tablets (6Weeks Supply)</div>
<div class="abs price-val" style="left:436px;top:1780px;width:100px;text-align:right">$160</div>

<div class="abs price-label" style="left:99px;top:1820px">40 Tablets (2Weeks Supply)</div>
<div class="abs price-val" style="left:102px;top:1845px">$80</div>
<div class="abs price-label" style="left:330px;top:1820px;width:210px;text-align:right">100 Tablets (8Weeks Supply)</div>
<div class="abs price-val" style="left:436px;top:1848px;width:100px;text-align:right">$200</div>

<div class="abs price-label" style="left:99px;top:1881px">80 Tablets (2Weeks Supply)</div>
<div class="abs price-val" style="left:102px;top:1906px">$100</div>
<div class="abs price-label" style="left:330px;top:1881px;width:210px;text-align:right">120 Tablets (8Weeks Supply)</div>
<div class="abs price-val" style="left:436px;top:1906px;width:100px;text-align:right">$240</div>

<div class="abs pills" role="img" aria-label="Pile of blue capsules and pink tablets"></div>

<div class="abs rule" style="left:99px;top:2020px;width:1002px"></div>

<div class="abs contact-ico" style="left:102px"><svg width="46" height="46"><path d="M15 12c2-2 4-1 5 1l2 4c1 2-1 3-2 4 1 3 3 5 6 6 1-1 2-3 4-2l4 2c2 1 3 3 1 5-3 3-8 3-14-3s-8-13-6-17z" fill="#fff"/></svg></div>
<div class="abs c-label" style="left:164px;top:2072px">CALL FOR CAPPOINMENT</div>
<div class="abs c-value" style="left:163px;top:2093px">(05)48127730</div>
<div class="abs vsep" style="left:388px"></div>

<div class="abs contact-ico" style="left:459px"><svg width="46" height="46"><rect x="9" y="13" width="28" height="20" fill="none" stroke="#fff" stroke-width="2"/><polyline points="9,13 23,25 37,13" fill="none" stroke="#fff" stroke-width="2"/><line x1="9" y1="33" x2="19" y2="23" stroke="#fff" stroke-width="2"/><line x1="37" y1="33" x2="27" y2="23" stroke="#fff" stroke-width="2"/></svg></div>
<div class="abs c-label" style="left:522px;top:2072px">EMAIL:</div>
<div class="abs c-small" style="left:522px;top:2094px">HELLO@BRIGHTLEAFRXPASS.INFO</div>
<div class="abs vsep" style="left:805px"></div>

<div class="abs contact-ico" style="left:870px"><svg width="46" height="46"><path d="M23 9c-6 0-10 4-10 10 0 7 10 18 10 18s10-11 10-18c0-6-4-10-10-10z" fill="#fff"/><circle cx="23" cy="19" r="4" fill="#1a4f98"/></svg></div>
<div class="abs c-small" style="left:934px;top:2072px">SUITE 7, 21 ELMWOOD ROW<br>FAIRVALE NSW</div>

<footer class="abs footer"></footer>
<nav class="abs foot-nav"><span>HOME</span><span>|</span><span>GET CARD</span><span>|</span><span>FAQ</span><span>|</span><span>PHARMACIES</span><span>|</span><span>DRUG PRICING</span><span>|</span><span>CONTACT</span></nav>
<div class="abs social" style="left:535px"></div>
<div class="abs social" style="left:582px"></div>
<div class="abs social" style="left:629px"></div>
<div class="abs copy">Copyright © 2013.All right reserved</div>
</body>
</html>
```